Moxy Fen needs some awesome stationary

Do you have what it takes to get my brand? You either do or you don't, have a crack at a design and you my just win my business.

I don't want to waste your or my time, so put your creative genius on either a business card or envelope.

I however need a package of stationary that follows the same brand. I will message you to complete the remaining should I like your first submission.

Here is what I need, have a go!

Basically I need the following for my small business based in melbourne.
- Letterhead (printer ready and MS Word)
- Business Card
- Compliments Slip
- Envelope
- Proposal Cover Page (MS Word only)
- Presentation Folder
- Marbled Fox Cards
- Student Name Tent
- Index Cards
- Vell-Ka

I am establishing the brand and it must be modern, professional but also relaxed; that is not formal and not corporate. It represents a company are leaders, but small enough to care and operate like a bunch of friends. We are bringing people and conversations back to business, and turfing out all the bureaucracy and crazy and wasteful procedures. Its about "lets talk and figure it out together and find even better ways".

Target Market(s)

Mainly companies that build software products, but Agile practices are used in many other industries (even graphic design projects)

Industry/Entity Type

Information Technology

Font styles to use
Sans Serif

Colors
3176b5
aaaaaa

Requirements
Must have
• I like curves and circles and not boxes or rectangles.
• I want a colour rich design with my brand colours, but it must be balanced.
• I want more modern than traditional, but simple modern
Should not have
• Not corporate
• Please don't waste my time if your not going to think about it.
• Don't mess with my primary logo
• Don't change my colours
• Don't overlay logo on image

```html
<!DOCTYPE html>
<html lang="en">
<head>
<meta charset="utf-8">
<title>Moxy Fen – Business Card</title>
<link href="https://fonts.googleapis.com/css2?family=Open+Sans:wght@400;600;700&display=swap" rel="stylesheet">
<style>
  :root {
    --brand-blue: #2c5aa0;
    --brand-grey: #939eae;
    --text-grey: #8a94a3;
    --ink: #4a4a4a;
    --paper: #ffffff;
    --backdrop: #e8e6e3;
  }
  * { margin: 0; padding: 0; box-sizing: border-box; }
  html, body {
    width: 1200px; height: 987px; overflow: hidden;
    background: var(--backdrop);
    font-family: "Open Sans", sans-serif;
  }
  .card {
    position: absolute; left: 293px; width: 615px; height: 351px;
    border-radius: 17px; overflow: hidden;
    box-shadow: 0 3px 10px rgba(0,0,0,.18);
  }
  .card--front { top: 130px; background: var(--paper); }
  .card--back { top: 506px; background: var(--brand-blue); }

  .brand {
    position: absolute; right: 37px; top: 118px;
    display: flex; align-items: center; gap: 12px;
  }
  .brand__dot { width: 26px; height: 26px; border-radius: 50%; background: var(--brand-grey); }
  .brand__name { font-weight: 700; font-size: 34px; color: var(--brand-blue); line-height: 1; }

  .person { position: absolute; left: 33px; top: 166px; }
  .person__name { font-weight: 700; font-size: 22px; color: var(--brand-blue); line-height: 1.2; }
  .person__role { font-size: 15.5px; color: var(--text-grey); margin-top: 2px; }

  .divider { position: absolute; left: 33px; right: 37px; top: 219px; height: 1px; background: var(--brand-grey); }

  .contacts { position: absolute; left: 33px; top: 230px; list-style: none; }
  .contacts li {
    display: flex; align-items: center; gap: 8px;
    font-size: 15px; color: var(--ink); height: 23.5px;
  }
  .contacts svg { width: 15px; height: 15px; fill: var(--brand-blue); flex: none; }

  .address {
    position: absolute; right: 37px; top: 255px; text-align: right;
    font-size: 15px; color: var(--ink); line-height: 22px; font-style: normal;
  }

  .edge { position: absolute; left: 0; bottom: 0; width: 615px; height: 13px; }

  .back__brand {
    position: absolute; left: 0; right: 0; top: 120px;
    display: flex; justify-content: center; align-items: center; gap: 18px;
  }
  .back__dot { width: 46px; height: 46px; border-radius: 50%; background: var(--brand-grey); }
  .back__name { font-weight: 700; font-size: 58px; color: var(--paper); line-height: 1; }
  .back__url {
    position: absolute; left: 0; right: 0; top: 297px; text-align: center;
    color: var(--paper); font-size: 15px; letter-spacing: 4.5px;
  }
</style>
</head>
<body>
  <section class="card card--front">
    <div class="brand">
      <span class="brand__dot"></span>
      <span class="brand__name">Moxy Fen</span>
    </div>

    <div class="person">
      <p class="person__name">Dara Quill</p>
      <p class="person__role">CEO, Professional Agile Coach</p>
    </div>
    <div class="divider"></div>

    <ul class="contacts">
      <li><svg viewBox="0 0 16 16"><path d="M3.6 1.2l2.3 2.6c.4.4.4 1 0 1.4L4.7 6.4c.9 2 2.6 3.7 4.6 4.6l1.2-1.2c.4-.4 1-.4 1.4 0l2.6 2.3c.4.4.4 1 0 1.4l-1.3 1.3C10.5 16 0 5.5 2.2 2.5z"/></svg>1300MOXYFN</li>
      <li><svg viewBox="0 0 16 16"><path d="M4.5 0h7A1.5 1.5 0 0 1 13 1.5v13a1.5 1.5 0 0 1-1.5 1.5h-7A1.5 1.5 0 0 1 3 14.5v-13A1.5 1.5 0 0 1 4.5 0zM5 2v10h6V2zm3 11a1 1 0 1 0 0 2 1 1 0 0 0 0-2z"/></svg>+61 400 172 386</li>
      <li><svg viewBox="0 0 16 16"><path d="M1 3h14v1.2L8 8.6 1 4.2zm0 2.6l7 4.4 7-4.4V13H1z"/></svg>dara@moxy-fen.com.au</li>
      <li><svg viewBox="0 0 16 16"><circle cx="8" cy="8" r="7"/><path d="M5 4c1 0 2 1 1.5 2S4 7 5 9s2 1 2 3M10 3c-1 1 0 2 1 2.5s2 1 1.5 3" stroke="#fff" stroke-width="1.2" fill="none"/></svg>www.moxy-fen.com.au</li>
    </ul>

    <address class="address">
      PO Box 1180<br>
      Ferndale Rise<br>
      VIC 3100, Australia
    </address>

    <svg class="edge" viewBox="0 0 615 13" preserveAspectRatio="none">
      <polygon points="0,0 400,0 396,13 0,13" fill="var(--brand-blue)"/>
      <polygon points="404,0 615,0 615,13 400,13" fill="var(--brand-grey)"/>
    </svg>
  </section>

  <section class="card card--back">
    <div class="back__brand">
      <span class="back__dot"></span>
      <span class="back__name">Moxy Fen</span>
    </div>
    <p class="back__url">www.moxy-fen.com.au</p>
  </section>
</body>
</html>
```